Velk Partners Building Business Cards

We need a business card that reflects our business as "Solar Experts" in San Diego. Browse our website www.velkpartners.example our License needs to be displayed as "CSLB# 3867140" our phone number is (619) 555-0187

Save thousands on your electric bills and increase the value of your home while helping to protect the environment. Our solar installation experts will help you design the system that's right for you, using only the highest quality equipment that will look great and give you ideal performance. Our goal is to make you energy independent, and get your electric bill to 0.

Paul Osterby
(619) 555-0187
paul@velkpartners.example

Target Market(s)

Home owners in san diego looking for solar

Industry/Entity Type

Solar Energy

Contact Information for Business Card

Paul Osterby
(619) 555-0187
paul@velkpartners.example

Font styles to use
Other font styles liked:
• Use our logo font

Requirements
Must have
• License needs to be displayed as "CSLB# 3867140" our phone number is (619) 555-0187
Nice to have
• Real images of rooftop home solar in san diego
Should not have
• our business address

```html
<!DOCTYPE html>
<html lang="en">
<head>
<meta charset="utf-8">
<title>Velk Partners Building – Business Card</title>
<link rel="stylesheet" href="https://fonts.googleapis.com/css2?family=Open+Sans:wght@400;600;700&display=swap">
<style>
  :root {
    --stage: #3b3330;
    --card-white: #fbfbfa;
    --navy: #1f3f7f;
    --ink: #2c2c2c;
    --sun: #f4ab00;
    --sky-top: #c9dcea;
    --panel-blue: #27407a;
    --panel-deep: #1a2c5c;
    --tile: #b8643c;
  }
  * { margin: 0; padding: 0; box-sizing: border-box; }
  html, body {
    width: 1200px; height: 844px; overflow: hidden;
    background: var(--stage);
    font-family: "Open Sans", Arial, sans-serif;
  }
  .canvas {
    width: 1200px; height: 844px;
    display: flex; align-items: center; justify-content: center; gap: 48px;
  }
  .card {
    width: 540px; height: 309px; border-radius: 3px; overflow: hidden;
    position: relative; box-shadow: 0 8px 24px rgba(0,0,0,.35);
  }
  /* Contact side */
  .card--contact { background: var(--card-white); }
  .brand-mark {
    position: absolute; left: 36px; bottom: 48px;
    display: flex; align-items: center; gap: 12px;
  }
  .brand-mark__dot { width: 34px; height: 34px; border-radius: 50%; background: var(--sun); }
  .brand-mark__name {
    font-weight: 700; font-size: 21px; color: var(--navy); line-height: 1.15; width: 170px;
  }
  .contact {
    position: absolute; left: 300px; top: 68px; color: var(--ink);
  }
  .contact__name {
    font-weight: 700; font-size: 16px; color: var(--navy);
    text-transform: uppercase; letter-spacing: .3px; margin-bottom: 30px;
  }
  .contact__line { display: flex; align-items: center; gap: 8px; font-size: 13.5px; margin-bottom: 4px; }
  .contact__line svg { width: 12px; height: 12px; fill: var(--navy); flex: none; }
  .contact__license { margin-top: 40px; font-size: 13.5px; }
  .contact__license span { color: var(--navy); font-weight: 600; }
  /* Photo side */
  .card--photo { background: var(--panel-deep); }
  .photo-fill {
    position: absolute; inset: 0;
    background:
      linear-gradient(160deg, var(--sky-top) 0%, #9fb9d4 18%, var(--panel-blue) 34%, var(--panel-deep) 70%, var(--tile) 100%);
  }
  .photo-title {
    position: absolute; left: 0; right: 0; top: 50%; transform: translateY(-50%);
    text-align: center; color: #ffffff; font-weight: 700; font-size: 38px; line-height: 1.1;
  }
</style>
</head>
<body>
<main class="canvas">
  <section class="card card--contact">
    <div class="brand-mark">
      <div class="brand-mark__dot"></div>
      <div class="brand-mark__name">Velk Partners Building</div>
    </div>
    <div class="contact">
      <p class="contact__name">Paul Osterby</p>
      <p class="contact__line">
        <svg viewBox="0 0 24 24" aria-hidden="true"><path d="M6.6 10.8a15.1 15.1 0 0 0 6.6 6.6l2.2-2.2a1 1 0 0 1 1-.25 11.4 11.4 0 0 0 3.6.57 1 1 0 0 1 1 1V20a1 1 0 0 1-1 1A17 17 0 0 1 3 4a1 1 0 0 1 1-1h3.5a1 1 0 0 1 1 1c0 1.25.2 2.45.57 3.57a1 1 0 0 1-.25 1z"/></svg>
        (619) 555-0187
      </p>
      <p class="contact__line">
        <svg viewBox="0 0 24 24" aria-hidden="true"><path d="M2 5h20v14H2z M2 5l10 8 10-8" fill="none" stroke="#1f3f7f" stroke-width="2.4"/></svg>
        paul@velkpartners.example
      </p>
      <p class="contact__license"><span>License:</span> CSLB# 3867140</p>
    </div>
  </section>

  <section class="card card--photo">
    <div class="photo-fill" role="img" aria-label="Photo of solar panels on a tiled rooftop under a blue sky"></div>
    <div class="photo-title">Velk Partners Building</div>
  </section>
</main>
</body>
</html>
```